Building company buisness cards

We are looking for a sharp modern new look for our business cards.
We are a New Zealand based company that specialises in house and land packages.
We have attached a photo of the current logo and would like to see if it can be improved somehow if needed.
We are open to any colours but we have chosen green at this stage.
Feel free to change the font and make the logo smarter looking.
Play with the colours and see what looks best.

We want a card that looks so good know one will want to throw it away!

Target Market(s)

Home buyers

Industry/Entity Type

Building

Contact Information for Business Card

Derek Tolvane
0217394062
dtolvane@quillmarkhomesteads.co.nz
quillmarkhomesteads.co.nz

Font styles to use
Serif
Sans Serif

Colors

Designer to choose colors to be used in the design.

Requirements
Must have
• Logo and company name on one side, details on the other side
Nice to have
• Color codes for the original green are HEX #4a8028, RGB(74,128,40), CMYK(42,0,69,50)
• Round corners, Raised and/or spot UV

```html
<!DOCTYPE html>
<html lang="en">
<head>
<meta charset="utf-8">
<title>Quillmark Homesteads – Business Cards</title>
<link rel="stylesheet" href="https://fonts.googleapis.com/css2?family=Open+Sans:wght@400;600;700;800&display=swap">
<style>
  :root {
    --backdrop: #3a322d;
    --card: #1d1e20;
    --green: #4a8028;
    --green-bright: #5a9a2f;
    --silver: #bfc1c3;
    --white: #f2f2f2;
    --divider: #8a8c8e;
  }
  * { box-sizing: border-box; margin: 0; padding: 0; }
  html, body { width: 1200px; height: 864px; overflow: hidden; }
  body {
    background: var(--backdrop);
    font-family: "Open Sans", sans-serif;
    position: relative;
  }
  .card {
    position: absolute;
    width: 540px;
    height: 310px;
    background: var(--card);
    border-radius: 10px;
    box-shadow: 0 14px 30px rgba(0,0,0,.45);
    overflow: hidden;
  }
  .card--front { left: 40px; top: 110px; }
  .card--back { left: 620px; top: 440px; }

  /* front */
  .front-brand {
    position: absolute;
    left: 0; right: 0; top: 92px;
    text-align: center;
    color: var(--silver);
    font-weight: 800;
    line-height: 1.0;
  }
  .front-brand__mark {
    display: block;
    width: 18px; height: 18px;
    margin: 0 auto 12px;
    background: var(--silver);
  }
  .front-brand__line1 { font-size: 26px; display: block; }
  .front-brand__line2 { font-size: 34px; display: block; }
  .front-web {
    position: absolute;
    left: 0; right: 0; bottom: 56px;
    text-align: center;
    color: var(--silver);
    font-size: 15px;
    letter-spacing: 3px;
  }

  /* back */
  .back-brand {
    position: absolute;
    left: 32px; top: 96px;
    width: 170px;
    color: var(--green-bright);
    font-weight: 700;
    font-size: 24px;
    line-height: 1.1;
  }
  .back-brand__mark {
    display: block;
    width: 22px; height: 22px;
    background: var(--green-bright);
    margin-bottom: 14px;
  }
  .back-divider {
    position: absolute;
    left: 214px; top: 70px;
    width: 1px; height: 170px;
    background: var(--divider);
  }
  .contact {
    position: absolute;
    left: 232px; top: 108px;
    right: 14px;
  }
  .contact__name {
    color: var(--green-bright);
    font-weight: 700;
    font-size: 21px;
    letter-spacing: .5px;
    margin-bottom: 10px;
  }
  .contact__row {
    display: flex;
    align-items: center;
    gap: 8px;
    color: var(--white);
    font-size: 13.5px;
    line-height: 24px;
    white-space: nowrap;
  }
  .contact__icon { width: 13px; height: 13px; flex: none; }
</style>
</head>
<body>
  <section class="card card--front" aria-label="Card front">
    <div class="front-brand">
      <span class="front-brand__mark"></span>
      <span class="front-brand__line1">quillmark</span>
      <span class="front-brand__line2">homesteads.</span>
    </div>
    <p class="front-web">www.quillmarkhomesteads.co.nz</p>
  </section>

  <section class="card card--back" aria-label="Card back">
    <div class="back-brand">
      <span class="back-brand__mark"></span>
      quillmark homesteads
    </div>
    <div class="back-divider"></div>
    <div class="contact">
      <p class="contact__name">DEREK TOLVANE</p>
      <p class="contact__row">
        <svg class="contact__icon" viewBox="0 0 16 16" aria-hidden="true"><path fill="#5a9a2f" d="M3 1h3l1.5 4-2 1.3a9 9 0 0 0 4.2 4.2l1.3-2 4 1.5v3a2 2 0 0 1-2 2A13 13 0 0 1 1 3a2 2 0 0 1 2-2z"/></svg>
        0217394062
      </p>
      <p class="contact__row">
        <svg class="contact__icon" viewBox="0 0 16 16" aria-hidden="true"><rect x="1" y="3" width="14" height="10" rx="1.5" fill="#5a9a2f"/><path d="M1.5 4l6.5 5 6.5-5" fill="none" stroke="#1d1e20" stroke-width="1.4"/></svg>
        dtolvane@quillmarkhomesteads.co.nz
      </p>
      <p class="contact__row">
        <svg class="contact__icon" viewBox="0 0 16 16" aria-hidden="true"><circle cx="8" cy="8" r="7" fill="#5a9a2f"/><path d="M1 8h14M8 1c-3 3.5-3 10.5 0 14M8 1c3 3.5 3 10.5 0 14" fill="none" stroke="#1d1e20" stroke-width="1.2"/></svg>
        quillmarkhomesteads.co.nz
      </p>
    </div>
  </section>
</body>
</html>
```